Veltrano.co - Polar Expeditions Specialists

We need a modern, visually striking business card for Veltrano.co, a company specialized in selling expedition cruises to the most remote regions on Earth, with a focus on the Arctic and Antarctica. The design should instantly communicate that the cardholder is an expert in polar travel. Use clean, premium aesthetics with cool tones like icy blue and white, possibly incorporating polar imagery (ice, glaciers, penguins, etc.)

Attached the logo

Contact Information for Business Card

Feels high-end and trustworthy.. Visually memorable — encourages people to keep it

Colors
0054AA
0677BA
7BADD7
CADEEF
E8F1F8

Requirements
Must have
• ice, glaciers, penguins, montains
Nice to have
• modern, transparente,

```html
<!DOCTYPE html>
<html lang="en">
<head>
<meta charset="utf-8">
<title>Veltrano.co – Business Card</title>
<link href="https://fonts.googleapis.com/css2?family=Poppins:wght@600;700&family=Montserrat:wght@400;500&display=swap" rel="stylesheet">
<style>
  :root {
    --page-bg: #e4e3e6;
    --card-white: #ffffff;
    --brand-blue: #3668b5;
    --back-blue: #3677b6;
    --back-mark: #0d56a6;
    --back-tagline: #1f5fa8;
    --ink: #151515;
  }
  * { margin: 0; padding: 0; box-sizing: border-box; }
  html, body {
    width: 1200px; height: 1108px; overflow: hidden;
    background: var(--page-bg);
  }
  .card {
    position: absolute;
    left: 218px;
    width: 776px;
  }
  .card-front { top: 51px; height: 473px; background: var(--card-white); }
  .card-back { top: 568px; height: 457px; background: var(--back-blue); }

  .brand-name {
    font-family: "Poppins", sans-serif;
    font-weight: 700;
    letter-spacing: 0.3px;
    line-height: 1;
    white-space: nowrap;
  }
  .brand-tagline {
    font-family: "Poppins", sans-serif;
    font-weight: 600;
    line-height: 1;
    white-space: nowrap;
  }

  .front-brand {
    position: absolute;
    left: 96px; top: 286px; width: 280px;
    text-align: center;
    color: var(--brand-blue);
  }
  .front-brand .brand-name { font-size: 43px; }
  .front-brand .brand-tagline { font-size: 16px; margin-top: 9px; }

  .divider {
    position: absolute; left: 382px; top: 163px;
    width: 2px; height: 202px; background: var(--brand-blue);
  }
  .contact {
    position: absolute; left: 403px; top: 160px;
    font-family: "Montserrat", sans-serif; color: var(--ink);
  }
  .contact-name {
    font-family: "Poppins", sans-serif; font-weight: 600;
    font-size: 29px; color: var(--brand-blue); line-height: 1.1;
  }
  .contact-role { font-size: 18px; margin-top: 1px; }
  .contact-list { list-style: none; margin-top: 12px; }
  .contact-list li {
    display: flex; align-items: center; gap: 9px;
    font-size: 18px; height: 30px;
  }
  .contact-list svg { width: 17px; height: 17px; fill: var(--brand-blue); flex: none; }
  .contact-address { font-size: 18px; line-height: 22px; margin-top: 4px; }

  .back-brand {
    position: absolute;
    left: 272px; top: 206px;
  }
  .back-brand .brand-name { font-size: 63px; color: var(--back-mark); }
  .back-brand .brand-tagline { font-size: 23px; color: var(--back-tagline); margin-top: 14px; }
</style>
</head>
<body>
  <section class="card card-front" aria-label="Business card front">
    <div class="front-brand">
      <div class="brand-name">Veltrano.co</div>
      <div class="brand-tagline">Polar Expeditions Specialists</div>
    </div>
    <div class="divider"></div>
    <div class="contact">
      <div class="contact-name">Marcus Ellery</div>
      <div class="contact-role">Managing Director</div>
      <ul class="contact-list">
        <li>
          <svg viewBox="0 0 24 24" aria-hidden="true"><path d="M6.6 10.8a15.1 15.1 0 0 0 6.6 6.6l2.2-2.2c.3-.3.7-.4 1-.2 1.1.4 2.3.6 3.6.6.6 0 1 .4 1 1V20c0 .6-.4 1-1 1A17 17 0 0 1 3 4c0-.6.4-1 1-1h3.5c.6 0 1 .4 1 1 0 1.3.2 2.5.6 3.6.1.3 0 .7-.2 1l-2.3 2.2z"/></svg>
          (555)410-2286
        </li>
        <li>
          <svg viewBox="0 0 24 24" aria-hidden="true"><path d="M3 7.5V18h18V7.5l-9 6.5z M3.5 6h17L12 12z"/></svg>
          info@veltrano.co
        </li>
        <li>
          <svg viewBox="0 0 24 24" aria-hidden="true"><path d="M12 2a10 10 0 1 0 0 20 10 10 0 0 0 0-20zm-1 17.9A8 8 0 0 1 4.1 10l4.9 5v1a2 2 0 0 0 2 2zm6.9-2.5A2 2 0 0 0 16 16h-1v-3a1 1 0 0 0-1-1H8v-2h2a1 1 0 0 0 1-1V7h2a2 2 0 0 0 2-2v-.4a8 8 0 0 1 2.9 12.8z"/></svg>
          www.veltrano.co
        </li>
      </ul>
      <p class="contact-address">48 Glacier Point Drive<br>Northvale, ME 04210 USA</p>
    </div>
  </section>

  <section class="card card-back" aria-label="Business card back">
    <div class="back-brand">
      <div class="brand-name">Veltrano.co</div>
      <div class="brand-tagline">Polar Expeditions Specialists</div>
    </div>
  </section>
</body>
</html>
```